Northfield Builders Guild Business card

We are looking for a new business card design with photo included.
Our business is a nonprofit construction contractor membership organization. We offer business education, assist with business setup and licensing, provide safety training, and provide a member directory.
URL: www.builderslinkguild.org
Color code:
CMYK: 0 cyan, 42 magenta, 100 yellow, 0 black for Print.
Hexidecimal: #FF9900
RGB: R 255; G 153; B 0

```html
<!DOCTYPE html>
<html lang="en">
<head>
<meta charset="utf-8">
<title>Northfield Builders Guild — Business Card</title>
<link rel="stylesheet" href="https://fonts.googleapis.com/css2?family=Montserrat:wght@700;800&family=Arimo:wght@400&display=swap">
<style>
  :root {
    --brand-orange: #ff9900;
    --ink: #111111;
    --card-white: #f2f2f2;
    --card-black: #0c0c0c;
    --logo-grey: #8a8a8a;
    --backdrop: #2a2a2a;
    --body-text: #1a1a1a;
  }
  * { margin: 0; padding: 0; box-sizing: border-box; }
  html, body {
    width: 1200px; height: 1015px; overflow: hidden;
    background: var(--backdrop);
  }
  .sheet {
    width: 1200px; height: 1015px;
    display: flex; flex-direction: column; align-items: center; justify-content: center;
    gap: 56px;
  }
  .card {
    width: 700px; height: 400px; position: relative;
    box-shadow: 0 14px 36px rgba(0,0,0,.55);
  }
  /* Back side */
  .card--back {
    background: var(--card-black);
    display: flex; flex-direction: column; align-items: center; justify-content: center;
    gap: 54px;
  }
  .back-wordmark {
    font-family: "Montserrat", sans-serif; font-weight: 800;
    color: var(--logo-grey); font-size: 44px; line-height: 1.05;
    text-transform: uppercase; text-align: center; letter-spacing: .5px;
  }
  .back-url {
    font-family: "Arimo", sans-serif; font-size: 19px; letter-spacing: 2px;
    color: #d8d8d8;
  }
  /* Front side */
  .card--front { background: var(--card-white); padding: 44px 46px; }
  .front-wordmark {
    font-family: "Montserrat", sans-serif; font-weight: 800;
    font-size: 40px; line-height: 1; text-transform: uppercase;
    color: var(--ink); letter-spacing: -.5px;
  }
  .holder { position: absolute; left: 46px; top: 150px; }
  .holder-name {
    font-family: "Montserrat", sans-serif; font-weight: 800; font-size: 30px;
    color: var(--brand-orange); text-transform: uppercase; line-height: 1.1;
  }
  .holder-title {
    font-family: "Montserrat", sans-serif; font-weight: 700; font-size: 17px;
    color: var(--ink); text-transform: uppercase; letter-spacing: .5px; margin-top: 2px;
  }
  .contact-list { list-style: none; margin-top: 22px; }
  .contact-item {
    display: flex; align-items: center; gap: 10px;
    font-family: "Arimo", sans-serif; font-size: 18px; color: var(--body-text);
    line-height: 1; margin-bottom: 8px;
  }
  .contact-icon { width: 24px; height: 24px; flex: none; }
  .office {
    position: absolute; right: 46px; top: 190px; text-align: left;
    font-family: "Arimo", sans-serif; font-size: 18px; line-height: 1.3; color: var(--body-text);
  }
  .office-url { color: var(--brand-orange); margin-top: 16px; display: block; }
</style>
</head>
<body>
<main class="sheet">
  <section class="card card--back" aria-label="Card back">
    <p class="back-wordmark">Northfield<br>Builders Guild</p>
    <p class="back-url">www.builderslinkguild.org</p>
  </section>

  <section class="card card--front" aria-label="Card front">
    <p class="front-wordmark">Northfield Builders Guild</p>

    <div class="holder">
      <p class="holder-name">Daniel Reyes</p>
      <p class="holder-title">Managing Director</p>
      <ul class="contact-list">
        <li class="contact-item">
          <svg class="contact-icon" viewBox="0 0 24 24" aria-hidden="true"><circle cx="12" cy="12" r="12" fill="var(--brand-orange)"/><path d="M8 6.5l2 .2.8 2.6-1.4 1a7 7 0 0 0 4.3 4.3l1-1.4 2.6.8.2 2c-4.8.8-10.3-4.7-9.5-9.5z" fill="#fff"/></svg>
          (555) 214-7730
        </li>
        <li class="contact-item">
          <svg class="contact-icon" viewBox="0 0 24 24" aria-hidden="true"><circle cx="12" cy="12" r="12" fill="var(--brand-orange)"/><rect x="8.5" y="5.5" width="7" height="13" rx="1.2" fill="none" stroke="#fff" stroke-width="1.6"/><circle cx="12" cy="16" r=".9" fill="#fff"/></svg>
          800-555-0192
        </li>
        <li class="contact-item">
          <svg class="contact-icon" viewBox="0 0 24 24" aria-hidden="true"><circle cx="12" cy="12" r="12" fill="var(--brand-orange)"/><rect x="8.5" y="6" width="7" height="4" fill="#fff"/><rect x="6" y="10" width="12" height="5.5" rx="1" fill="#fff"/><rect x="8.5" y="14" width="7" height="4" fill="#fff" stroke="var(--brand-orange)" stroke-width=".8"/></svg>
          555.310.0448
        </li>
        <li class="contact-item">
          <svg class="contact-icon" viewBox="0 0 24 24" aria-hidden="true"><circle cx="12" cy="12" r="12" fill="var(--brand-orange)"/><rect x="6" y="8" width="12" height="8.5" fill="#fff"/><path d="M6 8l6 5 6-5" fill="none" stroke="var(--brand-orange)" stroke-width="1.2"/></svg>
          support@nbguild.org
        </li>
      </ul>
    </div>

    <address class="office" style="font-style:normal">
      4200 Ridgeview Ave<br>
      Suite #210, Millbrook<br>
      OR 97000
      <span class="office-url">www.builderslinkguild.org</span>
    </address>
  </section>
</main>
</body>
</html>
```